Norrell Advisory WA Business Card

Create an interesting, eye catching and colourful two sided business card. We are a business consulting operation assisting SME's improve all areas of their business. We provide consulting services to assist SME's to create a culture of continuous improvement, making a positive difference in the business. Our tag line is Small changes, big rewards. We want to create a well recognised, innovative brand that can be continued throughout our website, social media and email correspondence.

Target Market(s)

Small to Medium Enterprise Business Owners

Industry/Entity Type

Business Consultant

Contact Information for Business Card

Name of Business: Norrell Advisory - Small Changes Big Rewards
Derek Holloway Ph 0407385510 Megan Holloway Ph 0407913847
Email norrelladvisorywa@mailbox-example.com
Web address TBA
FaceBook page TBA

BACKSIDE OF CARD

Providing assistance with:

• Organisation & Efficiency
• Revenue generation & Marketing
• Financial Management
• Production quality & delivery
• Systems & Process documentation
• Exit Strategy

Font styles to use
Other font styles liked:
• Calibri

Colors

Designer to choose colors to be used in the design.

Requirements
Must have
• Calibri font

```html
<!DOCTYPE html>
<html lang="en">
<head>
<meta charset="utf-8">
<title>Norrell Advisory WA Business Card</title>
<link rel="stylesheet" href="https://fonts.googleapis.com/css2?family=Carlito:wght@400;700&display=swap">
<style>
  :root {
    --backdrop: #58585c;
    --card: #ffffff;
    --brand-red: #e8392b;
    --brand-blue: #0f6aa0;
    --heading-blue: #1f6fb5;
    --ink: #222222;
    --on-blue: #ffffff;
  }
  * { box-sizing: border-box; margin: 0; padding: 0; }
  html, body {
    width: 1200px; height: 1000px; overflow: hidden;
    background: var(--backdrop);
    font-family: "Carlito", "Calibri", sans-serif;
  }
  .canvas { position: relative; width: 1200px; height: 1000px; }

  .card {
    position: absolute;
    width: 620px; height: 354px;
    background: var(--card);
    border-radius: 22px;
    overflow: hidden;
    box-shadow: 0 10px 30px rgba(0,0,0,.35);
  }
  .card--services { left: 470px; top: 70px; }
  .card--contact { left: 110px; top: 500px; }

  .brand {
    position: absolute; left: 0; right: 0;
    display: flex; align-items: center; justify-content: center; gap: 12px;
  }
  .brand__mark {
    width: 22px; height: 22px; border-radius: 50%;
    background: var(--brand-blue);
  }
  .brand__name {
    color: var(--brand-red);
    font-weight: 700; font-size: 30px; letter-spacing: .5px;
    text-transform: uppercase;
  }

  .card--services .brand { top: 148px; }
  .services { position: absolute; left: 0; right: 0; top: 212px; text-align: center; }
  .services__headline {
    color: var(--heading-blue); font-weight: 700; font-size: 17px; letter-spacing: .3px;
    margin-bottom: 8px;
  }
  .services__list { color: var(--ink); font-size: 15px; line-height: 1.35; }

  .card--contact .brand { top: 118px; }
  .tagline {
    position: absolute; left: 0; right: 0; top: 158px;
    text-align: center; color: var(--ink); font-size: 14px; letter-spacing: .8px;
  }
  .band-stripe {
    position: absolute; left: 0; right: 0; top: 194px; height: 6px;
    background: var(--brand-red);
  }
  .band {
    position: absolute; left: 0; right: 0; top: 204px; bottom: 0;
    background: var(--brand-blue);
    color: var(--on-blue);
    display: flex; align-items: center;
    padding: 0 30px;
  }
  .people { width: 210px; text-align: right; padding-right: 20px; }
  .person + .person { margin-top: 10px; }
  .person__name { font-weight: 700; font-size: 22px; text-transform: uppercase; line-height: 1.05; }
  .person__phone { font-size: 21px; display: flex; align-items: center; justify-content: flex-end; gap: 8px; line-height: 1.1; }
  .divider { width: 2px; height: 110px; background: var(--on-blue); }
  .links { padding-left: 20px; font-size: 17px; }
  .links__item { display: flex; align-items: center; gap: 10px; line-height: 1.6; }
  .icon { width: 16px; height: 16px; flex: none; }
  .icon--dot { width: 12px; height: 12px; margin: 0 2px; border-radius: 50%; background: var(--on-blue); }
</style>
</head>
<body>
<main class="canvas">

  <section class="card card--services">
    <div class="brand">
      <span class="brand__mark"></span>
      <span class="brand__name">Norrell Advisory</span>
    </div>
    <div class="services">
      <p class="services__headline">CREATING A CULTURE OF CONTINUOUS IMPROVEMENT</p>
      <p class="services__list">Organisation &amp; Efficiency | Revenue generation &amp; Marketing | Financial Management<br>
      Production quality &amp; delivery | Systems &amp; Process documentation | Exit Strategy</p>
    </div>
  </section>

  <section class="card card--contact">
    <div class="brand">
      <span class="brand__mark"></span>
      <span class="brand__name">Norrell Advisory</span>
    </div>
    <p class="tagline">SMALL CHANGES * BIG REWARDS</p>
    <div class="band-stripe"></div>
    <div class="band">
      <div class="people">
        <div class="person">
          <p class="person__name">Derek Holloway</p>
          <p class="person__phone">0407385510
            <svg class="icon" viewBox="0 0 16 16" aria-hidden="true"><path fill="#fff" d="M3.6 1.2l2.3 2.7-1.3 1.6c.9 2 2.6 3.7 4.6 4.6l1.6-1.3 2.7 2.3-1.4 2.4C6.6 13.4 2.6 9.4 1.2 3.9z"/></svg>
          </p>
        </div>
        <div class="person">
          <p class="person__name">Megan Holloway</p>
          <p class="person__phone">0407913847
            <svg class="icon" viewBox="0 0 16 16" aria-hidden="true"><path fill="#fff" d="M3.6 1.2l2.3 2.7-1.3 1.6c.9 2 2.6 3.7 4.6 4.6l1.6-1.3 2.7 2.3-1.4 2.4C6.6 13.4 2.6 9.4 1.2 3.9z"/></svg>
          </p>
        </div>
      </div>
      <div class="divider"></div>
      <div class="links">
        <p class="links__item">
          <svg class="icon" viewBox="0 0 16 16" aria-hidden="true"><rect x="1" y="3" width="14" height="10" rx="1" fill="#fff"/><path d="M1.5 3.5L8 9l6.5-5.5" stroke="#0f6aa0" stroke-width="1.4" fill="none"/></svg>
          norrelladvisorywa@mailbox-example.com
        </p>
        <p class="links__item">
          <svg class="icon" viewBox="0 0 16 16" aria-hidden="true"><g fill="none" stroke="#fff" stroke-width="1.4"><circle cx="8" cy="8" r="6.5"/><ellipse cx="8" cy="8" rx="3" ry="6.5"/><path d="M1.5 8h13"/></g></svg>
          www.norrelladvisory.com
        </p>
        <p class="links__item">
          <span class="icon icon--dot"></span>
          norrelladvisory
        </p>
      </div>
    </div>
  </section>

</main>
</body>
</html>
```